Postcard Design

Brivola Ftness Center is a state of the art equine rehabilitation and fitness center. We offer a wide variety of options to get your equine partner in tip top performing condition. Whether is swimming in or 11 foot deep pool or exercising in the squatted, we provide a personalized program for your special horse. Some other services offered are Tandoril breathing treatments, pelto drift and rostanel.
Updates
Project Deadline Extended Reason: Since the project was started we have opened for business and I have pictures using my equipment at our place of business that I would like to add to the project to be used. I have also received my logo design from one of your designers that I would like added to this project. Added Tuesday, March 15, 2016
Industry/Entity Type
Fitness
Look and feel
Each slider illustrates characteristics of the customer's brand and the style your logo design should communicate.

```html
<!DOCTYPE html>
<html lang="en">
<head>
<meta charset="utf-8">
<title>Brivola Ftness Center – Postcard</title>
<link href="https://fonts.googleapis.com/css2?family=Dancing+Script:wght@500;700&family=Merriweather:wght@400&display=swap" rel="stylesheet">
<style>
:root{
  --page:#e9e4de;
  --card:#ffffff;
  --cream:#f3dcc3;
  --teal:#1e8a92;
  --ink:#2b1a14;
  --wood-light:#8a3a1c;
  --wood-dark:#5e2210;
  --rule:#6b6b6b;
}
*{margin:0;padding:0;box-sizing:border-box}
html,body{width:960px;height:1200px;overflow:hidden;background:var(--page)}
.canvas{position:relative;width:960px;height:1200px}
.postcard{position:absolute;left:133px;width:704px;height:544px;background:var(--card);box-shadow:0 4px 14px rgba(0,0,0,.18)}
.postcard--front{top:42px}
.postcard--back{top:618px}
.postcard svg.shapes{position:absolute;left:0;top:0}
.script{font-family:"Dancing Script",cursive;font-weight:700}
.serif{font-family:"Merriweather",serif}
.front-tagline{position:absolute;left:0;width:704px;top:334px;text-align:center;font-size:17.5px;line-height:23px;color:var(--ink)}
.front-tagline .brand{color:var(--teal);font-family:"Dancing Script",cursive;font-weight:500;font-size:21px}
.front-title{position:absolute;left:0;width:704px;top:446px;text-align:center;font-size:56px;color:#fff;text-shadow:0 3px 4px rgba(0,0,0,.45)}
.back-title{position:absolute;left:8px;width:422px;top:30px;text-align:center;font-size:33px;color:var(--teal)}
.back-copy{position:absolute;left:54px;width:370px;top:330px;font-size:12.6px;line-height:16.8px;color:var(--ink)}
.back-copy p{margin-bottom:5px}
.back-copy ul{list-style:none}
.back-copy li::before{content:"• "}
.back-band-text{position:absolute;left:8px;width:422px;top:492px;text-align:center;font-family:"Dancing Script",cursive;font-weight:500;font-size:15.5px;line-height:17px;color:#fff}
</style>
</head>
<body>
<div class="canvas">

  <section class="postcard postcard--front">
    <svg class="shapes" width="704" height="544" viewBox="0 0 704 544">
      <defs>
        <linearGradient id="woodFront" x1="0" y1="0" x2="0" y2="1">
          <stop offset="0" stop-color="var(--wood-light)"/>
          <stop offset="1" stop-color="var(--wood-dark)"/>
        </linearGradient>
        <linearGradient id="horseArt" x1="0" y1="0" x2="1" y2="1">
          <stop offset="0" stop-color="#111"/>
          <stop offset=".45" stop-color="#2a6f8f"/>
          <stop offset=".7" stop-color="#d8a23a"/>
          <stop offset="1" stop-color="#1a1a1a"/>
        </linearGradient>
      </defs>
      <rect class="panel" x="8" y="8" width="688" height="528" fill="var(--cream)"/>
      <path class="art-frame" role="img" aria-label="Colourful painted horse head on a black background"
        d="M190 42 H516 Q518 62 536 66 V120 Q546 180 536 240 V294 Q518 298 516 318 H190 Q188 298 170 294 V240 Q160 180 170 120 V66 Q188 62 190 42 Z"
        fill="url(#horseArt)" stroke="#fff" stroke-width="3"/>
      <path class="wood-band" d="M8 438 C120 420 250 396 320 394 C338 394 345 406 352 412 C359 406 366 394 384 394 C454 396 584 420 696 438 V536 H8 Z"
        fill="url(#woodFront)" stroke="#fff" stroke-width="2.5"/>
      <line x1="8" y1="436" x2="696" y2="436" stroke="#4a1a0b" stroke-width="2" opacity=".6"/>
    </svg>
    <p class="front-tagline serif"><span class="brand">Brivola Ftness Center</span> is a state of the art equine<br>rehabilitation and fitness center.</p>
    <h1 class="front-title script">Brivola Ftness Center</h1>
  </section>

  <section class="postcard postcard--back">
    <svg class="shapes" width="704" height="544" viewBox="0 0 704 544">
      <defs>
        <linearGradient id="woodBack" x1="0" y1="0" x2="0" y2="1">
          <stop offset="0" stop-color="var(--wood-light)"/>
          <stop offset="1" stop-color="var(--wood-dark)"/>
        </linearGradient>
        <linearGradient id="poolPhoto" x1="0" y1="0" x2="0" y2="1">
          <stop offset="0" stop-color="#6b5a4a"/>
          <stop offset=".45" stop-color="#4fb3b8"/>
          <stop offset="1" stop-color="#3a8f96"/>
        </linearGradient>
      </defs>
      <rect class="panel" x="8" y="8" width="422" height="528" fill="var(--cream)"/>
      <path class="photo-frame" role="img" aria-label="Photo of a dark horse standing in an exercise pool"
        d="M92 86 H346 Q348 102 366 106 V150 Q376 200 366 250 V296 Q348 300 346 316 H92 Q90 300 72 296 V250 Q62 200 72 150 V106 Q90 102 92 86 Z"
        fill="url(#poolPhoto)" stroke="#fff" stroke-width="3"/>
      <path class="wood-band" d="M8 487 C80 480 150 470 200 468 C210 468 214 474 219 478 C224 474 228 468 238 468 C288 470 358 480 430 487 V536 H8 Z"
        fill="url(#woodBack)" stroke="#fff" stroke-width="2"/>
      <rect class="stamp-box" x="613.5" y="40.5" width="81" height="77" fill="none" stroke="var(--rule)" stroke-width="1"/>
      <g class="address-lines" stroke="var(--rule)" stroke-width="1">
        <line x1="463" y1="180.5" x2="668" y2="180.5"/>
        <line x1="463" y1="215.5" x2="668" y2="215.5"/>
        <line x1="463" y1="250.5" x2="668" y2="250.5"/>
        <line x1="463" y1="286.5" x2="668" y2="286.5"/>
        <line x1="463" y1="321.5" x2="668" y2="321.5"/>
      </g>
    </svg>
    <h2 class="back-title script">Brivola Ftness Center</h2>
    <div class="back-copy serif">
      <p>We offer a wide variety of options to get your equine partner in tip top performing condition. Whether is swimming in or 11 foot deep pool or exercising in the squatted, we provide a personalized program for your special horse.</p>
      <p>Some other services offered are:</p>
      <ul>
        <li>Tandoril breathing treatments</li>
        <li>Pelto drift</li>
        <li>Rostanel</li>
      </ul>
    </div>
    <p class="back-band-text">Brivola Ftness Center is a state of the art equine<br>rehabilitation and fitness center.</p>
  </section>

</div>
</body>
</html>
```